New stationary design for online film company

We need some new stationary to fit with our new logo. The stationary should be professional, clean and simple.
We need designs for a full set of business stationary.
We need - letterhead, envelopes, invoices, proposals, coverslip/note and cover page

Industry/Entity Type

Business

```html
<!DOCTYPE html>
<html lang="en">
<head>
<meta charset="utf-8">
<title>reelvista stationery</title>
<link rel="stylesheet" href="https://fonts.googleapis.com/css2?family=Source+Sans+3:wght@400;600&display=swap">
<style>
  :root{
    --navy:#0d4670;
    --sky:#6aa3c4;
    --paper:#ffffff;
    --paper-shade:#f3f3f3;
    --ink:#333b44;
    --stage:#e8e5e1;
    --ghost:#dcdfe7;
    --line:#5a5f66;
  }
  *{box-sizing:border-box;margin:0;padding:0}
  html,body{width:1200px;height:486px;overflow:hidden}
  body{background:var(--stage);font-family:"Source Sans 3",sans-serif;color:var(--ink);position:relative}
  .sheet{position:absolute;background:linear-gradient(160deg,var(--paper) 40%,var(--paper-shade));box-shadow:0 1px 3px rgba(0,0,0,.18);overflow:hidden}
  .brand{position:absolute;display:flex;align-items:center;gap:4px;color:var(--navy);font-weight:600;letter-spacing:-.3px;line-height:1;z-index:1}
  .brand-dot{border-radius:50%;background:var(--navy);flex:none}
  .letterhead{top:18px;width:332px;height:430px}
  .letterhead.one{left:10px}
  .letterhead.two{left:374px}
  .letterhead .brand{left:98px;top:20px;font-size:23px}
  .letterhead.two .brand{left:12px}
  .letterhead .brand-dot{width:19px;height:19px}
  .ghost-mark{position:absolute;left:84px;top:155px;width:156px;height:156px;border-radius:50%;border:22px solid var(--ghost)}
  .foot-line{position:absolute;left:0;right:0;bottom:10px;text-align:center;font-size:5.6px;white-space:nowrap}
  .foot-line span+span{margin-left:6px;padding-left:6px;border-left:1px solid #aaa}
  .contact-block{position:absolute;right:18px;top:20px;font-size:5.6px;line-height:8px;padding-left:6px;border-left:1px solid #ccc}
  .wave{position:absolute;left:0;bottom:0;width:100%}
  .letterhead .wave{height:44px}
  .wave-address{position:absolute;right:18px;color:#fff;font-size:6px;line-height:7.5px;z-index:1}
  .letterhead .wave-address{bottom:8px}
  .option-label{position:absolute;top:462px;width:332px;text-align:center;font-size:23px;color:var(--navy);font-weight:400}
  .option-label.one{left:10px}
  .option-label.two{left:374px}
  .envelope{position:absolute;width:372px;height:166px}
  .envelope-art{position:absolute;inset:0;width:100%;height:100%}
  .env-back{left:824px;top:4px}
  .env-flap{left:740px;top:76px}
  .env-front{left:780px;top:150px;background:var(--paper);box-shadow:0 1px 3px rgba(0,0,0,.2);overflow:hidden}
  .env-front .brand{left:10px;top:12px;font-size:18px}
  .env-front .brand-dot{width:15px;height:15px}
  .env-front .return-address{position:absolute;left:31px;top:34px;font-size:5.4px}
  .env-front .wave{height:54px}
  .env-front .wave-address{bottom:12px;font-size:7px;letter-spacing:1.6px}
  .card{position:absolute;top:346px;width:185px;height:104px;border-radius:9px;overflow:hidden;box-shadow:0 1px 3px rgba(0,0,0,.2)}
  .card-front{left:774px;background:var(--paper)}
  .card-front .brand{left:10px;top:12px;font-size:18px}
  .card-front .brand-dot{width:15px;height:15px}
  .card-name{position:absolute;left:16px;top:38px;font-size:6.6px;font-weight:600;color:var(--navy)}
  .card-name em{font-style:normal;font-weight:400;color:var(--sky)}
  .card-contacts{position:absolute;left:16px;top:49px;font-size:5.2px;line-height:6.8px;list-style:none}
  .card-contacts li::before{content:"";display:inline-block;width:3.5px;height:3.5px;border-radius:50%;background:var(--ink);margin-right:3px}
  .card-front .wave{height:38px}
  .card-front .wave-address{bottom:4px;right:14px;font-size:5.2px;line-height:6.6px}
  .card-back{left:974px;background:var(--sky)}
  .card-back .solo-mark{position:absolute;left:72px;top:28px;width:40px;height:40px;border-radius:50%;background:var(--navy)}
  .card-back .card-url{position:absolute;left:0;right:0;top:82px;text-align:center;color:#fff;font-size:5.6px;letter-spacing:1.4px}
</style>
</head>
<body>

<section class="sheet letterhead one" aria-label="Letterhead option 1">
  <div class="brand"><span class="brand-dot"></span>reelvista</div>
  <div class="ghost-mark" aria-hidden="true"></div>
  <p class="foot-line"><span>Street Name, City Name, State Zip Code</span><span>555-014-2290</span><span>info@reelvista.com</span><span>www.reelvista.com</span></p>
</section>

<section class="sheet letterhead two" aria-label="Letterhead option 2">
  <div class="brand"><span class="brand-dot"></span>reelvista</div>
  <div class="contact-block">555-014-2290<br>info@reelvista.com<br>www.reelvista.com</div>
  <svg class="wave" viewBox="0 0 332 44" preserveAspectRatio="none" aria-hidden="true">
    <path d="M0 2 C30 40 120 26 200 16 C260 8 300 4 332 8 L332 44 L0 44 Z" fill="var(--navy)"/>
    <path d="M24 36 C110 36 200 18 325 10" stroke="#fff" stroke-width="1.2" fill="none"/>
  </svg>
  <p class="wave-address">Street Name, City Name<br>State Zip Code</p>
</section>

<p class="option-label one">Option-1</p>
<p class="option-label two">Option-2</p>

<div class="envelope env-back" aria-label="Envelope back with flap">
  <svg class="envelope-art" viewBox="0 0 372 166" preserveAspectRatio="none" aria-hidden="true">
    <rect width="372" height="166" fill="var(--paper)"/>
    <path d="M0 0 H372 V20 C330 50 230 66 186 68 C140 66 40 50 0 20 Z" fill="var(--sky)"/>
    <circle cx="186" cy="42" r="13" fill="var(--paper)"/>
  </svg>
</div>

<div class="envelope env-flap" aria-label="Envelope back, outlined flap">
  <svg class="envelope-art" viewBox="0 0 372 166" preserveAspectRatio="none" aria-hidden="true">
    <rect width="372" height="166" fill="var(--paper)"/>
    <path d="M0 0 C10 20 25 28 60 38 L186 66 L312 38 C347 28 362 20 372 0" stroke="var(--line)" stroke-width="1" fill="none"/>
    <circle cx="186" cy="44" r="13" fill="var(--navy)"/>
  </svg>
</div>

<section class="envelope env-front" aria-label="Envelope front">
  <div class="brand"><span class="brand-dot"></span>reelvista</div>
  <p class="return-address">Street Name, City Name, State Zip Code</p>
  <svg class="wave" viewBox="0 0 372 54" preserveAspectRatio="none" aria-hidden="true">
    <path d="M0 0 C20 40 110 30 200 20 C280 12 330 8 372 10 L372 54 L0 54 Z" fill="var(--navy)"/>
    <path d="M30 42 C120 42 220 22 362 14" stroke="#fff" stroke-width="1.2" fill="none"/>
  </svg>
  <p class="wave-address">www.reelvista.com</p>
</section>

<section class="card card-front" aria-label="Business card front">
  <div class="brand"><span class="brand-dot"></span>reelvista</div>
  <p class="card-name">Your Name, <em>Title</em></p>
  <ul class="card-contacts">
    <li>555-014-2290</li>
    <li>555-014-2291</li>
    <li>info@reelvista.com</li>
    <li>www.reelvista.com</li>
  </ul>
  <svg class="wave" viewBox="0 0 185 38" preserveAspectRatio="none" aria-hidden="true">
    <path d="M0 20 C30 32 80 16 120 8 C150 3 170 3 185 6 L185 38 L0 38 Z" fill="var(--navy)"/>
    <path d="M10 32 C60 30 110 14 180 8" stroke="#fff" stroke-width="1" fill="none"/>
  </svg>
  <p class="wave-address">Street Name, City Name<br>State Zip Code</p>
</section>

<section class="card card-back" aria-label="Business card back">
  <div class="solo-mark" aria-hidden="true"></div>
  <p class="card-url">www.reelvista.com</p>
</section>

</body>
</html>
```